Upmarket Dessert Lounge needs a Business Card Design

We are an upmarket dessert lounge needing a business card to match our image.

We want something that is simple yet beautiful, feminine, classy, sophisticated and elegant. We want it to stand out and don't mind if it is bold.

The design should include our logo and colours of red or maroon with gold highlights. We don't mind if black is used.

Marlow & Quince

Target Market(s)

For those who like to indulge or treat themselves and give in to their temptations on good quality desserts.

Industry/Entity Type

Business

Requirements
Must have
• Must include our logo and our name

Marlow & Quince

M & Q

```html
<!DOCTYPE html>
<html lang="en">
<head>
<meta charset="utf-8">
<title>Marlow &amp; Quince — Business Card</title>
<link href="https://fonts.googleapis.com/css2?family=Open+Sans:wght@400;600;700&display=swap" rel="stylesheet">
<style>
  :root {
    --maroon: #7a1315;
    --gold: #f6cb92;
    --white: #ffffff;
    --ink: #333333;
    --backdrop: #d6d6d6;
  }
  * { margin: 0; padding: 0; box-sizing: border-box; }
  html, body {
    width: 956px;
    height: 1200px;
    overflow: hidden;
    background: var(--backdrop);
    font-family: "Open Sans", sans-serif;
  }
  .card {
    position: absolute;
    left: 75px;
    width: 797px;
    height: 455px;
    border-radius: 28px;
    overflow: hidden;
  }
  .card--front { top: 86px; background: var(--white); }
  .card--back { top: 634px; background: var(--maroon); }

  .front__brand-side {
    position: absolute;
    left: 0; top: 0;
    width: 437px; height: 100%;
  }
  .front__divider {
    position: absolute;
    left: 437px; top: 0;
    width: 6px; height: 100%;
    background: var(--gold);
  }
  .front__info-side {
    position: absolute;
    left: 443px; top: 0; right: 0; height: 100%;
    background: var(--maroon);
    color: var(--white);
  }

  .brand-name {
    position: absolute;
    left: 0; right: 0;
    text-align: center;
    font-weight: 600;
    letter-spacing: 2px;
  }
  .front__brand-side .brand-name {
    top: 140px;
    font-size: 64px;
    color: var(--maroon);
  }
  .card--back .brand-name {
    top: 198px;
    font-size: 46px;
    color: var(--gold);
  }

  .address {
    position: absolute;
    left: 0; right: 0; top: 362px;
    text-align: center;
    font-size: 19px;
    line-height: 26px;
    color: var(--ink);
  }

  .person { position: absolute; left: 33px; top: 66px; }
  .person__name { font-size: 22px; font-weight: 700; line-height: 30px; }
  .person__role { font-size: 22px; font-weight: 400; line-height: 30px; letter-spacing: 0.5px; }

  .contact {
    position: absolute;
    left: 38px;
    list-style: none;
    font-size: 19px;
  }
  .contact li { height: 36px; line-height: 26px; }
  .contact--phones { top: 201px; }
  .contact--web { top: 351px; }
  .contact--web li { height: 33px; }
  .contact__label { font-weight: 700; }
</style>
</head>
<body>
  <section class="card card--front">
    <div class="front__brand-side">
      <div class="brand-name">M &amp; Q</div>
      <p class="address">0000, Street Name<br>City Name, Country Code.</p>
    </div>
    <div class="front__divider"></div>
    <div class="front__info-side">
      <div class="person">
        <p class="person__name">Your Name</p>
        <p class="person__role">Designation</p>
      </div>
      <ul class="contact contact--phones">
        <li><span class="contact__label">p</span> : 123-456-7890</li>
        <li><span class="contact__label">c</span> : 123-456-7890</li>
        <li><span class="contact__label">f</span> : 123-456-7890</li>
      </ul>
      <ul class="contact contact--web">
        <li><span class="contact__label">e</span> : name@yourwebsite.com</li>
        <li><span class="contact__label">w</span> : www.marlow&amp;quince.com</li>
      </ul>
    </div>
  </section>

  <section class="card card--back">
    <div class="brand-name">MARLOW &amp; QUINCE</div>
  </section>
</body>
</html>
```